Business Card Design For Marketing Agnecy LVP

Need business card design for marketing agency.

Doug Fenwick
President, CEO
1-555-302-4196
doug@boldpromoperksgroup.example
www.BoldPromoPerksGroup.example

Back Side:
Boost Sales Using Rewards, Incentives & Giveaways
Get A Free Sample Package

Target Market(s)

B2B

Industry/Entity Type

Marketing

Contact Information for Business Card

Doug Fenwick
President, CEO
1-555-302-4196

Back Side:
Get A Free Sample Package

Please note that my current url is OLD DESIGN. I am working on new design and want the business card to match color themes at least on new site. Here is the demo link for new site so you can see the colors I use, etc.

http://layoutcratehub.example/kq/doug/lvp_final/index.html

Requirements
Must have
• Please note that my current url is OLD DESIGN. I am working on new design and want the business card to match color themes at least on new site. Here is the demo link for new site so you can see the colors I use, etc.

Nice to have

Should not have

```html
<!DOCTYPE html>
<html lang="en">
<head>
<meta charset="utf-8">
<title>Bold Promo Perks Group — Business Card</title>
<link rel="stylesheet" href="https://fonts.googleapis.com/css2?family=Montserrat:wght@400;500;600;800&display=swap">
<style>
  :root {
    --backdrop: #1b1b1d;
    --card-dark: #1f1f21;
    --card-light: #ffffff;
    --brand-blue: #1f73c4;
    --text-light: #f2f2f2;
    --text-dark: #3a3a3c;
  }
  * { box-sizing: border-box; margin: 0; padding: 0; }
  html, body { width: 1200px; height: 852px; overflow: hidden; }
  body {
    background: var(--backdrop);
    font-family: "Montserrat", sans-serif;
    position: relative;
  }
  .card {
    position: absolute;
    width: 540px;
    height: 308px;
    border-radius: 18px;
    box-shadow: 0 14px 36px rgba(0,0,0,0.55);
  }
  .card--back {
    left: 40px; top: 110px;
    background: var(--card-dark);
    color: var(--text-light);
    text-align: center;
    padding-top: 52px;
  }
  .card--front {
    left: 620px; top: 430px;
    background: var(--card-light);
    color: var(--text-dark);
  }
  .wordmark {
    color: var(--brand-blue);
    font-weight: 800;
    text-transform: uppercase;
    letter-spacing: 0.02em;
  }
  .card--back .wordmark { font-size: 34px; line-height: 1.05; }
  .card--back .wordmark-rule {
    width: 340px; height: 2px; margin: 10px auto 0;
    background: var(--brand-blue);
  }
  .tagline {
    margin-top: 22px;
    font-size: 15px;
    font-weight: 500;
  }
  .cta {
    display: block;
    width: 452px;
    margin: 12px auto 0;
    padding: 15px 0;
    background: var(--brand-blue);
    border-radius: 4px;
    color: #fff;
    font-size: 19px;
    font-weight: 800;
    letter-spacing: 0.05em;
    text-transform: uppercase;
  }
  .card--back .site { margin-top: 16px; font-size: 16px; font-weight: 500; }

  .logo-block {
    position: absolute; right: 34px; top: 44px;
    display: flex; align-items: center; gap: 10px;
  }
  .logo-dot { width: 16px; height: 16px; border-radius: 50%; background: var(--brand-blue); }
  .card--front .wordmark { font-size: 22px; text-align: right; line-height: 1.1; }
  .divider {
    position: absolute; left: 34px; right: 34px; top: 138px;
    height: 2px; background: var(--brand-blue);
  }
  .person { position: absolute; left: 34px; top: 162px; }
  .person-name { color: var(--brand-blue); font-size: 22px; font-weight: 600; text-transform: uppercase; }
  .person-title { font-size: 15px; margin-top: 2px; }
  .person-rule { width: 200px; height: 1.5px; background: var(--brand-blue); margin-top: 10px; }
  .contacts { list-style: none; margin-top: 10px; font-size: 14px; }
  .contacts li { display: flex; align-items: center; gap: 9px; line-height: 1.5; }
  .contacts svg { width: 12px; height: 12px; fill: none; stroke: var(--brand-blue); stroke-width: 2; }
</style>
</head>
<body>
  <section class="card card--back">
    <div class="wordmark">Bold Promo<br>Perks Group</div>
    <div class="wordmark-rule"></div>
    <p class="tagline">Boost Sales Using Rewards, Incentives &amp; Giveaways</p>
    <span class="cta">Get a Free Sample Package</span>
    <p class="site">www.BoldPromoPerksGroup.example</p>
  </section>

  <section class="card card--front">
    <div class="logo-block">
      <span class="logo-dot"></span>
      <div class="wordmark">Bold Promo<br>Perks Group</div>
    </div>
    <div class="divider"></div>
    <div class="person">
      <h1 class="person-name">Doug Fenwick</h1>
      <p class="person-title">President, CEO</p>
      <div class="person-rule"></div>
      <ul class="contacts">
        <li><svg viewBox="0 0 12 12"><path d="M3 1 L5 3 L4 5 Q5 7 7 8 L9 7 L11 9 L9 11 Q2 10 1 3 Z"/></svg>1-555-302-4196</li>
        <li><svg viewBox="0 0 12 12"><rect x="1" y="2.5" width="10" height="7"/><path d="M1 2.5 L6 6.5 L11 2.5"/></svg>doug@boldpromoperksgroup.example</li>
        <li><svg viewBox="0 0 12 12"><circle cx="6" cy="6" r="5"/><path d="M1 6 H11 M6 1 Q3 6 6 11 Q9 6 6 1"/></svg>www.BoldPromoPerksGroup.example</li>
      </ul>
    </div>
  </section>
</body>
</html>
```